Start up International Security Business Needs a Web Design

Based in Edinburgh UK, Morvane Global Services (www.morvanegs.example) provides security services of various types in challenging or high threat environments internationally for government and private sector organizations. We provide risk assessments, security audits and training, medical support, close protection for individuals, groups and events, crisis management, and evacuation coordination; we enable businesses to operate in challenging locations. Our experts are highly trained and qualified with exceptional experience worldwide.
The name Morvane was selected in competition and derives from Greek Mythology where it was a giant man of bronze gifted by Zeus to protect Europa from invaders and pirates, circling the island of Crete three times daily (essentially establishing a protective perimeter). The centre of the current logo (inside the "O") is a stylized symbol of Zeus; we use it as a customized "bullet" on documents and acts as an abbreviated logo.
We purposefully omitted any reference to security in the name/logo and the web-page should be discreet in the same manner - we provide services of this nature but do not draw attention to ourselves. Generic images for visuals should be used as opposed to any existing stock photography we possess as a company. Imagery that relay protection, an international reach, innovation, modern vistas, varied countrysides (desert, jungle, urban settings, an old fortress?) would be seen positively.
The current colour of blue and white in the principal logo has received positive response for the clean lines, and the grey-ish scale writing similarly works. The "O" with the symbol inside has been used as customized "bullets" inside of documents, and we envisioned several other potential uses for web pages, etc.
However the integration of bronze as a third colour given the origin of Morvane could be a consideration as well.
The final design should communicate clarity, an international reach in difficult areas with our broad experience and strength without being aggressive. There must be a section where the countries we have experience operating in is displayed graphically (i.e. a global map where the countries are coloured in). Countries are USA, Canada, UK, France, Bosnia, UAE, Qatar, Libya, Tunisia, Afghanistan, Iraq, Turkey, Sudan, Egypt, Central African Republic, Somalia, Rwanda, Somaliland. Additional sections should include "Our Clients", "Our Services", "Our Expertise", "Join Our Team" which should have a personal details form and ability to upload a CV, "Our Contact Details" which should also allow for submission of a web enquiry
Reason: Extension granted at the request of several designers in order to conceptualize solutions whilst initial selection process begins. Feedback on each design submitted will be provided. Very many thanks to all who took the time to share their vision for our company's website.
Morvane GS
Target Market(s)
Private Sector energy, logistics, and infrastructure companies along with government organizations
Industry/Entity Type
Security
Logo Text
Morvane
Number of Pages Required
3 page
Requirements
Must have
- There must be a section where the countries we have experience operating in is displayed graphically (i.e. a global map where the countries are coloured in). Countries are USA, Canada, UK, France, Bosnia, UAE, Qatar, Libya, Tunisia, Afghanistan, Iraq, Turkey, Sudan, Egypt, Central African Republic, Somalia, Rwanda, Somaliland. Additional sections should include "Our Clients", "Our Services", "Our Expertise", "Join Our Team" which should have a personal details form and ability to upload a CV, "Our Contact Details" which should also allow for submission of a web enquiry
Should not have
- Aggressive pictures of guards, weapons, etc

```html
<!DOCTYPE html>
<html lang="en">
<head>
<meta charset="utf-8">
<title>Morvane Global Services</title>
<link href="https://fonts.googleapis.com/css2?family=Lato:ital,wght@0,300;0,400;0,700;0,900;1,400&family=Open+Sans:wght@400;600;700&display=swap" rel="stylesheet">
<style>
:root{
  --brand:#1d5c96;
  --ink:#1f2330;
  --text:#555b66;
  --muted:#9aa0a8;
  --nav:#333;
  --nav-active:#1d6fb8;
  --white:#fff;
  --footer:#232323;
  --footer-line:#3a3a3a;
  --footer-text:#8d8d8d;
  --accent:#e7a64a;
  --tw:#39a9e0;
  --box-blue:#d7e3ee;
  --box-mint:#c8eee2;
  --box-pink:#f7d5d9;
  --box-grey:#d7dee0;
  --box-navy:#1d2436;
  --box-peach:#fde5d0;
  --box-lilac:#ecdae5;
}
*{margin:0;padding:0;box-sizing:border-box}
html,body{width:1200px;height:2744px;overflow:hidden}
body{position:relative;background:var(--white);font-family:"Lato",sans-serif;color:var(--text)}
.abs{position:absolute}

/* header */
.site-header{left:0;top:0;width:1200px;height:122px;background:var(--white)}
.logo{left:99px;top:22px;font-family:"Open Sans",sans-serif;font-weight:700;font-size:58px;color:var(--brand);letter-spacing:-1px;line-height:1}
.call{right:150px;top:32px;text-align:right;font-family:"Open Sans",sans-serif;color:#222;white-space:nowrap}
.call small{display:block;font-size:12px;line-height:16px}
.call strong{display:block;font-size:20px;line-height:26px;font-weight:400}
.call-dot{left:1069px;top:38px;width:32px;height:32px;border:3px solid var(--brand);border-radius:50%}
.main-nav{right:98px;top:90px;display:flex;gap:42px;font-family:"Open Sans",sans-serif;font-size:14px;color:var(--nav)}
.main-nav .active{color:var(--nav-active)}

/* hero */
.hero{left:0;top:122px;width:1200px;height:555px;background:radial-gradient(circle at 560px 180px,#8b2530 0%,#3b2a33 18%,#1c2229 40%,#14181d 70%,#3a3d40 100%)}
.hero-caption{left:90px;top:412px;width:605px;height:210px;background:rgba(25,25,25,.72);padding:34px 22px 34px 34px}
.hero-caption h1{font-family:"Open Sans",sans-serif;font-weight:700;font-size:40px;line-height:44px;color:var(--white);letter-spacing:1px}
.hero-caption p{font-family:"Open Sans",sans-serif;font-size:19px;line-height:27px;color:#eee;margin-top:14px}
.hero-arrow{top:380px}
.hero-dots{left:473px;top:480px;display:flex;gap:9px}
.hero-dots span{width:8px;height:8px;border-radius:50%;background:#888}
.hero-dots span.on{background:#ddd}

/* welcome */
.welcome-title{left:0;top:708px;width:1200px;text-align:center;font-family:"Open Sans",sans-serif;font-size:27px;font-weight:600;color:#111;letter-spacing:1px}
.welcome-text{left:110px;top:760px;width:980px;text-align:center;font-size:12.5px;line-height:19px;color:#555}

.service{width:372px}
.service h3{font-size:13px;font-weight:900;letter-spacing:1px;color:var(--ink);margin-bottom:10px}
.service p{font-size:11.5px;line-height:21px;color:var(--muted)}
.service.left{text-align:right}
.tile{width:103px;height:103px;display:flex;align-items:center;justify-content:center}
.tile.navy{outline:2px solid #6a7285;outline-offset:-7px}

/* tweets */
.tweets{left:0;top:1467px;width:1200px;height:411px;background:radial-gradient(ellipse at 600px 760px,#2c5a86 0%,#14304f 30%,#0a1626 60%,#060b14 100%)}
.tw-ring{left:550px;top:1470px;width:100px;height:100px;border-radius:50%;border:2px solid rgba(255,255,255,.6);display:flex;align-items:center;justify-content:center}
.tw-ring span{width:80px;height:80px;border-radius:50%;background:var(--white)}
.tw-title{left:0;top:1644px;width:1200px;text-align:center;font-size:32px;line-height:40px;font-weight:300;color:var(--white)}
.tw-quote{left:190px;top:1710px;width:820px;text-align:center;font-style:italic;font-size:20px;line-height:31px;color:var(--white)}
.tw-quote em{color:var(--accent)}
.tw-name{left:0;top:1795px;width:1200px;text-align:center;font-weight:700;font-size:14px;color:var(--white)}
.tw-rule{left:585px;top:1822px;width:30px;height:1px;background:#aaa}
.tw-time{left:0;top:1833px;width:1200px;text-align:center;font-size:11px;color:#ccc}

/* experience */
.exp-title{left:99px;top:2000px;font-family:"Open Sans",sans-serif;font-size:27px;font-weight:600;color:#111}
.exp-text{left:99px;top:2060px;width:350px;font-size:12.5px;line-height:18.5px;color:#555}
.map{left:497px;top:1972px;width:620px;height:388px;background:linear-gradient(135deg,#4aa2de 0%,#2d7fc4 55%,#1d64a8 100%);box-shadow:0 10px 14px rgba(0,0,0,.35)}

/* footer */
.site-footer{left:0;top:2478px;width:1200px;height:266px;background:var(--footer)}
.f-col{top:2510px;width:351px;text-align:center;font-size:11.5px;line-height:20px;color:var(--footer-text)}
.f-col svg{display:block;margin:0 auto 14px}
.f-div{top:2500px;width:1px;height:108px;background:var(--footer-line)}
.social{left:512px;top:2640px;display:flex;gap:14px}
.social span{width:24px;height:24px;border-radius:50%;background:#4a4a4a}
.social span.on{background:var(--tw)}
.copyright{left:0;top:2688px;width:1200px;text-align:center;font-size:11px;letter-spacing:1px;color:#6d6d6d}
</style>
</head>
<body>

<header class="abs site-header">
  <div class="abs logo">Morvane</div>
  <div class="abs call"><small>Call Us</small><strong>+ 44 131 555 0192</strong></div>
  <div class="abs call-dot"></div>
  <nav class="abs main-nav">
    <span class="active">Home</span><span>About us</span><span>Our Clients</span><span>Our Services</span><span>Our expertise</span><span>Join our team</span><span>Contact us</span>
  </nav>
</header>

<section class="abs hero" role="img" aria-label="Professional woman facing a large digital eye with a glowing red iris and data overlays"></section>
<svg class="abs hero-arrow" style="left:28px" width="24" height="34" viewBox="0 0 24 34"><path d="M19 3 5 17l14 14" fill="none" stroke="#fff" stroke-width="5"/></svg>
<svg class="abs hero-arrow" style="left:1150px" width="24" height="34" viewBox="0 0 24 34"><path d="M5 3l14 14L5 31" fill="none" stroke="#fff" stroke-width="5"/></svg>
<div class="abs hero-caption">
  <h1>MORVANE</h1>
  <p>We provide security services of various types in challenging or high threat environments internationally for government and private sector organizations.</p>
</div>
<div class="abs hero-dots"><span></span><span></span><span class="on"></span><span></span><span></span></div>

<h2 class="abs welcome-title">WELCOME</h2>
<p class="abs welcome-text">Donec ut mauris sit amet nunc feugiat pellentesque. Nulla ultrices nulla vitae turpis ultricies mollis. Nullam faucibus a augue nec placerat. Nullam a velit vitae erat posuere porta. Aliquam convallis blandit lacinia. Vivamus eu est massa. Morbi dolor tellus, auctor vel sapien id, posuere viverra purus. Nam ac nunc lectus. Cras mattis sollicitudin velit, et semper ex euismod sed. Cras eget vehicula dolor, id cursus purus. Ut sodales magna est, sed blandit tellus elementum a. Nullam sagittis quam nulla, sed lobortis nisi mollis eget. Proin efficitur sapien ante, ut venenatis urna varius eu. Donec non enim sit amet metus tempus pellentesque nec vitae odio. Nulla eu egestas sapien, sit amet auctor ex. Vivamus tempor vitae sem ac posuere.</p>

<!-- services: left column -->
<div class="abs service left" style="left:100px;top:889px"><h3>RISK ASSESSMENTS</h3><p>Phasellus ut condimentum diam, eget tempus lorem. Morbi bibendum est quis arcu posuere condimentum. Nullam justo eros, pellentesque a metus non, mattis volutpat libero. Praesent ornare felis ante.</p></div>
<div class="abs service left" style="left:100px;top:1017px"><h3>AND EVACUATION COORDINATION</h3><p>Phasellus ut condimentum diam, eget tempus lorem. Morbi bibendum est quis arcu posuere condimentum. Nullam justo eros, pellentesque a metus non, mattis volutpat libero. Praesent ornare felis ante.</p></div>
<div class="abs service left" style="left:100px;top:1145px"><h3>CRISIS MANAGEMENT</h3><p>Phasellus ut condimentum diam, eget tempus lorem. Morbi bibendum est quis arcu posuere condimentum. Nullam justo eros, pellentesque a metus non, mattis volutpat libero. Praesent ornare felis ante.</p></div>
<div class="abs service left" style="left:100px;top:1273px"><h3>GROUPS AND EVENTS</h3><p>Phasellus ut condimentum diam, eget tempus lorem. Morbi bibendum est quis arcu posuere condimentum. Nullam justo eros, pellentesque a metus non, mattis volutpat libero. Praesent ornare felis ante.</p></div>

<!-- services: tiles -->
<div class="abs tile" style="left:487px;top:893px;background:var(--box-blue)"><svg width="22" height="18" viewBox="0 0 22 18"><path d="M2 9l6 6L20 3" fill="none" stroke="#fff" stroke-width="4"/></svg></div>
<div class="abs tile" style="left:615px;top:893px;background:var(--box-mint)"><svg width="22" height="18" viewBox="0 0 22 18"><path d="M2 9l6 6L20 3" fill="none" stroke="#fff" stroke-width="4"/></svg></div>
<div class="abs tile" style="left:487px;top:1021px;background:var(--box-pink)"><svg width="22" height="18" viewBox="0 0 22 18"><path d="M2 9l6 6L20 3" fill="none" stroke="#fff" stroke-width="4"/></svg></div>
<div class="abs tile" style="left:615px;top:1021px;background:var(--box-grey)"><svg width="22" height="18" viewBox="0 0 22 18"><path d="M2 9l6 6L20 3" fill="none" stroke="#fff" stroke-width="4"/></svg></div>
<div class="abs tile navy" style="left:487px;top:1149px;background:var(--box-navy)"><svg width="22" height="18" viewBox="0 0 22 18"><path d="M2 9l6 6L20 3" fill="none" stroke="#fff" stroke-width="4"/></svg></div>
<div class="abs tile" style="left:615px;top:1149px;background:var(--box-peach)"><svg width="22" height="18" viewBox="0 0 22 18"><path d="M2 9l6 6L20 3" fill="none" stroke="#fff" stroke-width="4"/></svg></div>
<div class="abs tile" style="left:487px;top:1277px;background:var(--box-lilac)"><svg width="22" height="18" viewBox="0 0 22 18"><path d="M2 9l6 6L20 3" fill="none" stroke="#fff" stroke-width="4"/></svg></div>

<!-- services: right column -->
<div class="abs service" style="left:735px;top:889px"><h3>SECURITY AUDITS AND TRAINING</h3><p>Phasellus ut condimentum diam, eget tempus lorem. Morbi bibendum est quis arcu posuere condimentum. Nullam justo eros, pellentesque a metus non, mattis volutpat libero. Praesent ornare felis ante.</p></div>
<div class="abs service" style="left:735px;top:1017px"><h3>MEDICAL SUPPORT</h3><p>Phasellus ut condimentum diam, eget tempus lorem. Morbi bibendum est quis arcu posuere condimentum. Nullam justo eros, pellentesque a metus non, mattis volutpat libero. Praesent ornare felis ante.</p></div>
<div class="abs service" style="left:735px;top:1145px"><h3>CLOSE PROTECTION FOR INDIVIDUALS,</h3><p>Phasellus ut condimentum diam, eget tempus lorem. Morbi bibendum est quis arcu posuere condimentum. Nullam justo eros, pellentesque a metus non, mattis volutpat libero. Praesent ornare felis ante.</p></div>

<!-- tweets -->
<section class="abs tweets" role="img" aria-label="Night view of the earth from space with glowing network lines circling the globe"></section>
<div class="abs tw-ring"><span></span></div>
<h2 class="abs tw-title">Latest Tweets</h2>
<p class="abs tw-quote">Lorem ipsum dolor sit amet, consectetur adipiscing elit. Pellentesque suscipit arcu dui, non pulvinar massa feugiat at. <em>Fusce malesuada</em></p>
<div class="abs tw-name">Elias Norwood</div>
<div class="abs tw-rule"></div>
<div class="abs tw-time">2 minutes ago</div>

<!-- experience -->
<h2 class="abs exp-title">EXPERIENCE OPERATING</h2>
<p class="abs exp-text">Donec ut mauris sit amet nunc feugiat pellentesque. Nulla ultrices nulla vitae turpis ultricies mollis. Nullam faucibus a augue nec placerat. Nullam a velit vitae erat posuere porta. Aliquam convallis blandit lacinia. Vivamus eu est massa. Morbi dolor tellus, auctor vel sapien id, posuere viverra purus. Nam ac nunc lectus. Cras mattis sollicitudin velit, et semper ex euismod sed. Cras eget vehicula dolor, id cursus purus. Ut sodales magna est, sed blandit tellus elementum a. Nullam sagittis quam nulla, sed lobortis nisi mollis eget. Proin efficitur sapien ante, ut venenatis urna varius eu.</p>
<div class="abs map" role="img" aria-label="Folded blue world map with coloured pins marking the countries where the company has operated"></div>

<!-- footer -->
<footer class="abs site-footer"></footer>
<div class="abs f-col" style="left:78px">
  <svg width="16" height="16" viewBox="0 0 16 16"><path d="M4 1l3 3-2 2c1 2 3 4 5 5l2-2 3 3-2 3C7 15 1 9 1 3z" fill="#666"/></svg>
  t: +44 (0)131 555 0147<br>f: +44 (0)131 555 0148
</div>
<div class="abs f-div" style="left:417px"></div>
<div class="abs f-col" style="left:418px">
  <svg width="18" height="14" viewBox="0 0 18 14"><rect x="1" y="1" width="16" height="12" fill="none" stroke="#666" stroke-width="2"/><path d="M1 1l8 7 8-7" fill="none" stroke="#666" stroke-width="2"/></svg>
  e: enquiries@morvanegs.example
</div>
<div class="abs f-div" style="left:768px"></div>
<div class="abs f-col" style="left:769px">
  <svg width="14" height="18" viewBox="0 0 14 18"><path d="M7 1a6 6 0 0 0-6 6c0 4 6 10 6 10s6-6 6-10a6 6 0 0 0-6-6z" fill="none" stroke="#666" stroke-width="2"/><circle cx="7" cy="7" r="2" fill="#666"/></svg>
  Lorem ipsum, Level 4, Harlow House<br>12 Quarry Lane, Edinburgh, EH3 7QT
</div>
<div class="abs social"><span></span><span class="on"></span><span></span><span></span><span></span></div>
<div class="abs copyright">© 2015. YOURSITE. ALL RIGHTS RESERVED</div>

</body>
</html>
```